Gooey Tides

I am creating an online slime shop that will sell handmade custom slimes. I need to be able to have payment/shipping options and the ability to change product photos since the product and product name will change often

Target Market(s)

Slime

Industry/Entity Type

Retail - online sales

Coding

Coded - Design and coding required

Number of Pages Required

2 page

Font styles to use
Sans Serif

Colors
0094D4
00A9DD
6FCCEA
C7EBF8
E9F6FB
E54698
E96AAD
F1A4CE
F9D9EA
FCEFF6
A7469A
B969AE
D3A5CF
EDDBEB
F8F0F9

Requirements
Must have
• My logo, my domain, ability to change photos of products for sale, payment options, shipping options, social media links, contact us,

```html
<!DOCTYPE html>
<html lang="en">
<head>
<meta charset="utf-8">
<title>Gooey Tides — Handmade Custom Slime</title>
<link href="https://fonts.googleapis.com/css2?family=Montserrat:wght@400;500;600&family=Poppins:wght@400;500&display=swap" rel="stylesheet">
<style>
:root{
  --pink:#e54698;
  --pink-soft:#e96aad;
  --pink-pale:#f9dfec;
  --purple:#a7469a;
  --ink:#1b1b1b;
  --muted:#9a9a9a;
  --star:#f6a21a;
  --footer:#2e2e2e;
  --grey-band:#f2f2f2;
  --line:#d9d9d9;
}
*{box-sizing:border-box;margin:0;padding:0}
html,body{width:1200px;height:4065px;overflow:hidden;background:#fff}
body{position:relative;font-family:"Poppins",sans-serif;color:var(--ink)}
.abs{position:absolute}
.heading{font-family:"Montserrat",sans-serif;font-weight:500;letter-spacing:.5px;text-transform:uppercase}

.topbar{left:0;top:0;width:1200px;height:42px;background:#000;color:#fff;font-size:13px;display:flex;align-items:center;justify-content:center;gap:14px;font-family:"Montserrat",sans-serif}
.topbar b{color:var(--pink);font-weight:500}

.brand{display:flex;align-items:center;gap:10px;font-family:"Montserrat",sans-serif;font-weight:600;color:var(--purple);text-transform:uppercase;letter-spacing:2px}
.brand .dot{border-radius:50%;background:var(--purple)}
.search{left:776px;top:63px;width:195px;height:32px;border:1px solid #bbb;border-radius:16px;background:#eee;font-size:11px;padding:0 16px;display:flex;align-items:center;justify-content:space-between;font-family:"Montserrat",sans-serif}
.pill{background:var(--pink);color:#fff;border-radius:20px;display:flex;align-items:center;justify-content:center;font-family:"Montserrat",sans-serif;font-weight:500;text-transform:uppercase}
.nav{top:116px;left:478px;font-family:"Montserrat",sans-serif;font-size:13px;text-transform:uppercase}
.nav span{position:absolute;white-space:nowrap}
.nav .active{color:var(--pink)}

.hero{left:0;top:148px;width:1200px;height:443px;overflow:hidden;background:linear-gradient(100deg,#c9a07a 0%,#e7d3bf 35%,#b97c68 60%,#8aa6b6 85%,#9fc17a 100%)}
.ear{border-radius:50%;background:var(--purple)}
.bubble{border-radius:50%;background:var(--pink);color:#fff;text-align:center;display:flex;flex-direction:column;align-items:center}
.bubble h2{font-family:"Montserrat",sans-serif;font-weight:500;text-transform:uppercase}
.bubble p{font-size:14px;line-height:29px}
.ghost{border:1.5px solid #fff;border-radius:20px;color:#fff;text-transform:uppercase;font-family:"Montserrat",sans-serif;display:flex;align-items:center;justify-content:center}

.perk{top:607px;width:377px;height:109px;background:var(--pink-pale);display:flex;flex-direction:column;align-items:center;justify-content:center;gap:10px;font-family:"Montserrat",sans-serif;font-size:15px;text-transform:uppercase}

.section-title{width:1200px;left:0;text-align:center;color:var(--pink);font-size:31px}

.card{width:313px;height:453px;border:2px solid var(--line);border-radius:6px;background:#fff}
.card.hover{border-color:#f1a4ce;box-shadow:0 4px 10px rgba(229,70,152,.15)}
.card .photo{position:absolute;left:7px;top:7px;width:295px;height:251px;border-radius:4px;overflow:hidden}
.card.arrival .photo{top:20px;height:205px}
.card .row{position:absolute;left:0;width:100%;text-align:center}
.stars{color:var(--star);font-size:15px;letter-spacing:1px}
.stars small{color:var(--ink);font-size:13px;margin-left:8px;letter-spacing:0}
.name{font-family:"Montserrat",sans-serif;font-size:14px;text-transform:uppercase}
.price{font-size:15px;color:var(--pink)}
.price s{color:var(--muted);text-decoration:none;margin-left:4px}
.actions{display:flex;justify-content:center;align-items:center;gap:14px}
.buy{width:107px;height:33px;font-size:13px}
.cart{width:31px;height:31px;border-radius:50%;border:1.5px solid var(--line);display:flex;align-items:center;justify-content:center}
.ribbon{position:absolute;left:-30px;top:20px;width:140px;transform:rotate(-40deg);background:var(--pink);color:#fff;text-align:center;font-size:12px;font-family:"Montserrat",sans-serif;text-transform:uppercase;padding:2px 0}
.more{left:475px;width:250px;height:47px;border-radius:24px;font-size:16px}

.about{left:0;top:1957px;width:1200px;height:479px;overflow:hidden;background:linear-gradient(90deg,#c6c9c4 0%,#d7b79e 45%,#b8875b 70%,#a7b9c3 100%)}

.testi-band{left:0;top:3198px;width:1200px;height:547px;background:var(--grey-band)}
.side{top:3387px;width:155px;height:234px;background:#fff;box-shadow:0 2px 8px rgba(0,0,0,.12);font-size:9px;color:var(--muted);line-height:21px;padding-top:46px}
.main-quote{left:339px;top:3351px;width:524px;height:307px;background:#fff;box-shadow:0 3px 14px rgba(0,0,0,.18);text-align:center}
.main-quote p{position:absolute;left:36px;top:60px;width:452px;font-size:13px;line-height:29px}
.arrow{width:41px;height:41px;border-radius:50%;background:#fff;border:1px solid #ddd;display:flex;align-items:center;justify-content:center}

.footer{left:0;top:3745px;width:1200px;height:320px;background:var(--footer);color:#fff}
.footer h4{position:absolute;color:var(--pink);font-family:"Montserrat",sans-serif;font-weight:500;font-size:18px;text-transform:uppercase}
.footer .link{position:absolute;font-size:13px;font-family:"Montserrat",sans-serif;text-transform:uppercase}
.email{left:833px;top:108px;width:255px;height:34px;background:#3e3e3e;color:#888;font-size:12px;padding-left:12px;display:flex;align-items:center;font-family:"Montserrat",sans-serif}
.copy{left:0;width:1200px;top:280px;text-align:center;font-size:14px;font-family:"Montserrat",sans-serif;text-transform:uppercase}
.copy b{color:var(--pink);font-weight:400}
</style>
</head>
<body>

<div class="abs topbar">
  <svg width="22" height="14" viewBox="0 0 22 14"><rect x="0" y="1" width="13" height="9" fill="#fff"/><path d="M13 4h5l3 3v3h-8z" fill="#fff"/><circle cx="5" cy="12" r="2" fill="#fff"/><circle cx="17" cy="12" r="2" fill="#fff"/></svg>
  <span>$6.22 US FLAT RATE &amp; FREE SHIPPING AT <b>$99</b></span>
</div>

<header>
  <div class="abs brand" style="left:110px;top:80px;font-size:20px"><span class="dot" style="width:26px;height:26px"></span>Gooey Tides</div>
  <div class="abs search"><span>SEARCH...</span>
    <svg width="12" height="12" viewBox="0 0 12 12"><circle cx="5" cy="5" r="4" fill="none" stroke="#333" stroke-width="1.5"/><path d="M8 8l3 3" stroke="#333" stroke-width="1.5"/></svg></div>
  <div class="abs pill" style="left:982px;top:63px;width:106px;height:32px;font-size:13px">Buy Now</div>
  <nav class="abs nav">
    <span class="active" style="left:0">Home</span>
    <span style="left:82px">Products</span>
    <span style="left:200px">Blog</span>
    <span style="left:279px">Shop</span>
    <span style="left:359px">Reviews</span>
    <span style="left:465px">Contact Us</span>
  </nav>
  <svg class="abs" style="left:1064px;top:110px" width="26" height="24" viewBox="0 0 26 24"><path d="M1 3h4l3 12h12l3-9H7" fill="none" stroke="#111" stroke-width="2.2"/><circle cx="10" cy="20" r="2" fill="#111"/><circle cx="19" cy="20" r="2" fill="#111"/><circle cx="22" cy="4" r="4" fill="var(--pink)"/></svg>
</header>

<section class="abs hero" role="img" aria-label="Photo of a smiling woman and a young boy stretching slime in a bright playroom">
  <div class="abs ear" style="left:689px;top:33px;width:80px;height:80px"></div>
  <div class="abs ear" style="left:856px;top:33px;width:80px;height:80px"></div>
  <div class="abs bubble" style="left:629px;top:49px;width:394px;height:394px;padding-top:80px">
    <h2 style="font-size:28px;line-height:43px">Get your Gooey<br>Tides on!</h2>
    <p style="margin-top:14px;width:310px">Lorem ipsum dolor sit amet, consectetur adipiscing elit, sed do eiusmod tempor incididunt ut labore.</p>
    <div class="ghost" style="width:140px;height:40px;margin-top:22px;font-size:16px">Shop Now</div>
  </div>
</section>

<section>
  <div class="abs perk" style="left:17px">
    <svg width="36" height="36" viewBox="0 0 36 36"><circle cx="18" cy="18" r="15" fill="none" stroke="#111" stroke-width="2.5" stroke-dasharray="70 10"/><circle cx="18" cy="14" r="5" fill="#111"/><path d="M9 28c2-6 16-6 18 0" fill="#111"/></svg>
    Top customer service</div>
  <div class="abs perk" style="left:412px">
    <svg width="56" height="34" viewBox="0 0 56 34"><rect x="10" y="3" width="28" height="20" fill="#111"/><path d="M38 9h9l7 8v6H38z" fill="#111"/><circle cx="19" cy="27" r="5" fill="#111" stroke="var(--pink-pale)" stroke-width="2"/><circle cx="45" cy="27" r="5" fill="#111" stroke="var(--pink-pale)" stroke-width="2"/><path d="M0 8h8M2 14h7M0 20h8" stroke="#111" stroke-width="2.5"/></svg>
    Free delivery over $100</div>
  <div class="abs perk" style="left:806px">
    <svg width="38" height="38" viewBox="0 0 38 38"><path d="M19 1l5 4 6-1 2 6 5 4-3 5 3 5-5 4-2 6-6-1-5 4-5-4-6 1-2-6-5-4 3-5-3-5 5-4 2-6 6 1z" fill="#111"/><circle cx="19" cy="19" r="10" fill="#fff"/><path d="M14 19l4 4 7-8" fill="none" stroke="#111" stroke-width="3"/></svg>
    We focus on quality</div>
</section>

<h2 class="abs heading section-title" style="top:788px">Featured Product</h2>

<article class="abs card" style="left:110px;top:859px">
  <div class="photo" role="img" aria-label="Girl holding up pink fluffy slime" style="background:linear-gradient(135deg,#eceeef,#f3a6cf 45%,#e9d7cf 70%,#d8dadb)"></div>
  <div class="row stars" style="top:286px">★★★★★<small>(23)</small></div>
  <div class="row name" style="top:320px">Lorem ipsum dolor sit amet</div>
  <div class="row price" style="top:351px">$34.89<s>$45.90</s></div>
  <div class="row actions" style="top:390px"><div class="pill buy">Buy Now</div><div class="cart"><svg width="15" height="13" viewBox="0 0 15 13"><path d="M0 1h3l2 7h7l2-6H4z" fill="var(--pink)"/><circle cx="6" cy="11" r="1.4" fill="var(--pink)"/><circle cx="11" cy="11" r="1.4" fill="var(--pink)"/></svg></div></div>
</article>
<article class="abs card hover" style="left:443px;top:859px">
  <div class="photo" role="img" aria-label="Hands stretching glittery purple slime over tubs" style="background:linear-gradient(135deg,#f4c6d8,#c9b7e6 40%,#7fa3e6 60%,#e6e1dc)"><div class="ribbon">50% Off</div></div>
  <div class="row stars" style="top:286px">★★★★★<small>(19)</small></div>
  <div class="row name" style="top:320px">Lorem ipsum dolor sit amet</div>
  <div class="row price" style="top:351px">$23.29<s>$32.20</s></div>
  <div class="row actions" style="top:390px"><div class="pill buy">Buy Now</div><div class="cart"><svg width="15" height="13" viewBox="0 0 15 13"><path d="M0 1h3l2 7h7l2-6H4z" fill="var(--pink)"/><circle cx="6" cy="11" r="1.4" fill="var(--pink)"/><circle cx="11" cy="11" r="1.4" fill="var(--pink)"/></svg></div></div>
</article>
<article class="abs card" style="left:776px;top:859px">
  <div class="photo" role="img" aria-label="Jar of blue glitter slime among colourful slime tubs" style="background:linear-gradient(135deg,#c9a870,#3a4fb5 40%,#9a57d8 65%,#f3608e)"></div>
  <div class="row stars" style="top:286px">★★★★★<small>(45)</small></div>
  <div class="row name" style="top:320px">Lorem ipsum dolor sit amet</div>
  <div class="row price" style="top:351px">$23.52<s>$29.56</s></div>
  <div class="row actions" style="top:390px"><div class="pill buy">Buy Now</div><div class="cart"><svg width="15" height="13" viewBox="0 0 15 13"><path d="M0 1h3l2 7h7l2-6H4z" fill="var(--pink)"/><circle cx="6" cy="11" r="1.4" fill="var(--pink)"/><circle cx="11" cy="11" r="1.4" fill="var(--pink)"/></svg></div></div>
</article>

<article class="abs card" style="left:110px;top:1334px">
  <div class="photo" role="img" aria-label="Child's hands holding lilac slime" style="background:linear-gradient(135deg,#b9a7d6,#d9c6ee 50%,#c0aedc)"></div>
  <div class="row stars" style="top:286px">★★★★★<small>(10)</small></div>
  <div class="row name" style="top:320px">Lorem ipsum dolor sit amet</div>
  <div class="row price" style="top:351px">$12.65<s>$24.90</s></div>
  <div class="row actions" style="top:390px"><div class="pill buy">Buy Now</div><div class="cart"><svg width="15" height="13" viewBox="0 0 15 13"><path d="M0 1h3l2 7h7l2-6H4z" fill="var(--pink)"/><circle cx="6" cy="11" r="1.4" fill="var(--pink)"/><circle cx="11" cy="11" r="1.4" fill="var(--pink)"/></svg></div></div>
</article>
<article class="abs card" style="left:443px;top:1334px">
  <div class="photo" role="img" aria-label="Jars of pink, blue and green slime" style="background:linear-gradient(90deg,#d44db0,#1aa3d8 40%,#20b7d9 60%,#2fbf4a)"></div>
  <div class="row stars" style="top:286px">★★★★★<small>(45)</small></div>
  <div class="row name" style="top:320px">Lorem ipsum dolor sit amet</div>
  <div class="row price" style="top:351px">$21.75<s>$29.60</s></div>
  <div class="row actions" style="top:390px"><div class="pill buy">Buy Now</div><div class="cart"><svg width="15" height="13" viewBox="0 0 15 13"><path d="M0 1h3l2 7h7l2-6H4z" fill="var(--pink)"/><circle cx="6" cy="11" r="1.4" fill="var(--pink)"/><circle cx="11" cy="11" r="1.4" fill="var(--pink)"/></svg></div></div>
</article>
<article class="abs card" style="left:776px;top:1334px">
  <div class="photo" role="img" aria-label="Jars of purple and green slime with pink slime puddle" style="background:linear-gradient(135deg,#8fd66a,#b51fd0 40%,#e52fc9 65%,#f1eef0)"></div>
  <div class="row stars" style="top:286px">★★★★★<small>(56)</small></div>
  <div class="row name" style="top:320px">Lorem ipsum dolor sit amet</div>
  <div class="row price" style="top:351px">$66.22<s>$54.56</s></div>
  <div class="row actions" style="top:390px"><div class="pill buy">Buy Now</div><div class="cart"><svg width="15" height="13" viewBox="0 0 15 13"><path d="M0 1h3l2 7h7l2-6H4z" fill="var(--pink)"/><circle cx="6" cy="11" r="1.4" fill="var(--pink)"/><circle cx="11" cy="11" r="1.4" fill="var(--pink)"/></svg></div></div>
</article>

<div class="abs pill more" style="top:1828px">View More Products</div>

<section class="abs about" role="img" aria-label="Photo of a young girl stretching pink slime in a playroom">
  <div class="abs ear" style="left:154px;top:67px;width:84px;height:84px"></div>
  <div class="abs ear" style="left:338px;top:67px;width:84px;height:84px"></div>
  <div class="abs bubble" style="left:86px;top:80px;width:436px;height:436px;padding-top:72px">
    <h2 style="font-size:29px;line-height:48px">About Gooey<br>Tides</h2>
    <p style="margin-top:14px;width:340px;font-size:15px;line-height:33px">Lorem ipsum dolor sit amet, consectetur adipiscing elit, sed do eiusmod tempor incididunt ut labore.</p>
    <div class="ghost" style="width:168px;height:44px;margin-top:20px;font-size:17px">Learn More</div>
  </div>
</section>

<h2 class="abs heading section-title" style="top:2514px">New Arrivals</h2>

<article class="abs card arrival" style="left:110px;top:2599px;height:435px">
  <div class="photo" role="img" aria-label="Blue slime spilling from a tub" style="background:radial-gradient(ellipse at 45% 60%,#3f8df0 0%,#6aa9f5 30%,#fff 60%)"></div>
  <div class="row price" style="top:250px">$12.65<s>$24.90</s></div>
  <div class="row name" style="top:288px">Lorem ipsum dolor sit amet</div>
  <div class="row stars" style="top:321px">★★★★★<small>(10)</small></div>
  <div class="row actions" style="top:368px"><div class="pill buy">Buy Now</div><div class="cart"><svg width="15" height="13" viewBox="0 0 15 13"><path d="M0 1h3l2 7h7l2-6H4z" fill="var(--pink)"/><circle cx="6" cy="11" r="1.4" fill="var(--pink)"/><circle cx="11" cy="11" r="1.4" fill="var(--pink)"/></svg></div></div>
</article>
<article class="abs card arrival" style="left:443px;top:2599px;height:435px">
  <div class="photo" role="img" aria-label="Green slime spilling from a clear jar" style="background:radial-gradient(ellipse at 45% 58%,#5cc62a 0%,#8fdc5a 30%,#fff 60%)"></div>
  <div class="row price" style="top:250px">$21.75<s>$29.60</s></div>
  <div class="row name" style="top:288px">Lorem ipsum dolor sit amet</div>
  <div class="row stars" style="top:321px">★★★★★<small>(45)</small></div>
  <div class="row actions" style="top:368px"><div class="pill buy">Buy Now</div><div class="cart"><svg width="15" height="13" viewBox="0 0 15 13"><path d="M0 1h3l2 7h7l2-6H4z" fill="var(--pink)"/><circle cx="6" cy="11" r="1.4" fill="var(--pink)"/><circle cx="11" cy="11" r="1.4" fill="var(--pink)"/></svg></div></div>
</article>
<article class="abs card arrival" style="left:776px;top:2599px;height:435px">
  <div class="photo" role="img" aria-label="Pink and blue slime spilling from two jars" style="background:radial-gradient(ellipse at 35% 55%,#ee4fae 0%,#f27bc3 22%,transparent 42%),radial-gradient(ellipse at 62% 62%,#2e9ef0 0%,#6cbcf5 25%,#fff 52%)"></div>
  <div class="row price" style="top:250px">$66.22<s>$54.56</s></div>
  <div class="row name" style="top:288px">Lorem ipsum dolor sit amet</div>
  <div class="row stars" style="top:321px">★★★★★<small>(56)</small></div>
  <div class="row actions" style="top:368px"><div class="pill buy">Buy Now</div><div class="cart"><svg width="15" height="13" viewBox="0 0 15 13"><path d="M0 1h3l2 7h7l2-6H4z" fill="var(--pink)"/><circle cx="6" cy="11" r="1.4" fill="var(--pink)"/><circle cx="11" cy="11" r="1.4" fill="var(--pink)"/></svg></div></div>
</article>

<div class="abs pill more" style="top:3069px">View More Products</div>

<section>
  <div class="abs testi-band"></div>
  <h2 class="abs heading section-title" style="top:3250px">Our Testimonials</h2>
  <div class="abs side" style="left:222px;padding-left:40px;text-align:left">Lorem ipsum d<br>eiusmod temp<br>enim ad minim v<br>ut aliquip ex e<br>reprehenderit i</div>
  <div class="abs side" style="left:826px;padding-left:38px;text-align:left">ing elit, sed do<br>magna aliqua. Ut<br>llamco laboris nisi<br>irure dolor in<br>dolore eu</div>
  <div class="abs main-quote">
    <svg class="abs" style="left:222px;top:-20px" width="76" height="56" viewBox="0 0 76 56"><path d="M2 4h30v24c0 14-8 24-20 27l-3-6c7-3 10-9 10-15H2z" fill="var(--pink)"/><path d="M42 4h30v24c0 14-8 24-20 27l-3-6c7-3 10-9 10-15H42z" fill="var(--pink)"/></svg>
    <p>Lorem ipsum dolor sit amet, consectetur adipiscing elit, sed do eiusmod tempor incididunt ut labore et dolore magna aliqua. Ut enim ad minim veniam, quis nostrud exercitation ullamco laboris nisi ut aliquip ex ea commodo consequat.</p>
    <div class="abs" role="img" aria-label="Customer portrait" style="left:148px;top:194px;width:76px;height:76px;border-radius:50%;border:2px solid var(--pink);background:radial-gradient(circle,#e9d4c6,#b88a72)"></div>
    <div class="abs" style="left:257px;top:208px;color:var(--pink);font-family:Montserrat,sans-serif;font-size:16px;letter-spacing:1px">MARISOL</div>
    <div class="abs stars" style="left:257px;top:236px;font-size:21px">★★★★★</div>
  </div>
  <div class="abs arrow" style="left:118px;top:3485px"><svg width="14" height="12" viewBox="0 0 14 12"><path d="M13 6H2M6 1L1 6l5 5" fill="none" stroke="#111" stroke-width="2"/></svg></div>
  <div class="abs arrow" style="left:1032px;top:3485px"><svg width="14" height="12" viewBox="0 0 14 12"><path d="M1 6h11M8 1l5 5-5 5" fill="none" stroke="var(--pink)" stroke-width="2"/></svg></div>
</section>

<footer class="abs footer">
  <div class="abs brand" style="left:110px;top:130px;font-size:24px;color:var(--pink)"><span class="dot" style="width:30px;height:30px;background:var(--pink)"></span>Gooey Tides</div>
  <h4 style="left:489px;top:57px">Quick Links</h4>
  <span class="link" style="left:489px;top:106px">Home</span>
  <span class="link" style="left:489px;top:142px">Products</span>
  <span class="link" style="left:489px;top:178px">Blog</span>
  <span class="link" style="left:662px;top:106px">Shop</span>
  <span class="link" style="left:662px;top:142px">Reviews</span>
  <span class="link" style="left:662px;top:178px">Contact Us</span>
  <h4 style="left:836px;top:57px">Newsletter</h4>
  <div class="abs email">EMAIL ADDRESS</div>
  <div class="abs pill" style="left:833px;top:164px;width:94px;height:28px;font-size:10px">Subscribe</div>
  <div class="abs copy">@2024 Copyrights - <b>Gooey Tides</b> - All Rights Reserved</div>
</footer>

</body>
</html>
```